Velmor Spire Nine Flash website

we need a website to cater to 2 aspect of the business. We have Velmor spire residence and velmor spire office. For the office, we will get their inquire and arrange a face to face meetup to show them the office area for rent. For the residence side, it will need to be like staylane or roomvio.com. we want to allow them to book online for the date they need. We have a total of 10 different room configurations starting at $70 per night and up depending on the size of the room. example of the design is https://brisquelodge.com/

Target Market(s)

the website should have detail information on the layout, designs, and luxury of the building.

Industry/Entity Type

office and service appartment rental/lease

Coding

Coded - Design and coding required

Number of Pages Required

5+ page

Requirements
Must have
• a luxury perspective
Nice to have
• example https://brisquelodge.com/

```html
<!DOCTYPE html>
<html lang="en">
<head>
<meta charset="utf-8">
<title>Velmor Spire Nine</title>
<link rel="stylesheet" href="https://fonts.googleapis.com/css2?family=Montserrat:ital,wght@0,400;0,500;1,400;1,500;1,600&display=swap">
<style>
  :root {
    --gold: #d4a02c;
    --gold-soft: #e0c27a;
    --navy: #1d3a5a;
    --navy-deep: #12304e;
    --ink: #1e1e1e;
    --body: #3a3a3a;
    --white: #ffffff;
  }
  * { margin: 0; padding: 0; box-sizing: border-box; }
  html, body { width: 1200px; height: 1200px; overflow: hidden; }
  body {
    position: relative;
    background: var(--white);
    font-family: "Montserrat", sans-serif;
    color: var(--ink);
  }
  .gold-band { position: absolute; left: 0; top: 0; width: 247px; height: 1200px; background: var(--gold); }

  /* Experience page peek */
  .experience-panel { position: absolute; left: 247px; top: 0; width: 548px; height: 209px; background: var(--white); }
  .experience-title {
    position: absolute; left: 38px; top: 70px;
    font-size: 30px; font-style: italic; font-weight: 600; letter-spacing: 0.3px; white-space: nowrap;
  }
  .experience-rule { position: absolute; left: 38px; top: 114px; width: 426px; height: 1px; background: var(--gold-soft); }
  .experience-text {
    position: absolute; left: 38px; top: 141px; width: 430px;
    font-size: 13px; font-style: italic; line-height: 20px; color: var(--body);
  }
  .lounge-photo {
    position: absolute; left: 795px; top: 0; width: 405px; height: 297px;
    background: linear-gradient(135deg, #6d6a66 0%, #a9a7a4 45%, #d6d4d1 75%, #8f8a84 100%);
  }
  .side-panel { position: absolute; left: 1110px; top: 297px; width: 90px; height: 502px; background: var(--white); }
  .side-rule { position: absolute; left: 0; top: 245px; width: 90px; height: 1px; background: var(--gold-soft); }
  .side-text {
    position: absolute; left: -3px; top: 272px; font-size: 13px; font-style: italic; color: var(--body); white-space: nowrap;
  }
  .pool-photo {
    position: absolute; left: 1110px; top: 799px; width: 90px; height: 351px;
    background: linear-gradient(180deg, #3b3b38 0%, #8a6a48 25%, #b08456 55%, #5fb7bf 78%, #8fd6dc 100%);
  }

  /* Home page */
  .home-page {
    position: absolute; left: 34px; top: 209px; width: 1076px; height: 991px;
    background: var(--white); border-top-left-radius: 12px; overflow: hidden;
  }
  .hero {
    position: absolute; left: 0; top: 0; width: 1076px; height: 583px;
    background: linear-gradient(160deg, #38495e 0%, #2c4a6a 40%, #1f4468 70%, var(--navy-deep) 100%);
  }
  .hero-photo {
    position: absolute; left: 310px; top: 145px; width: 470px; height: 438px;
    background: linear-gradient(180deg, rgba(120,110,100,0.55) 0%, rgba(90,95,105,0.6) 60%, rgba(60,70,85,0.6) 100%);
    clip-path: polygon(55% 0, 62% 4%, 100% 40%, 100% 100%, 0 100%, 5% 55%, 28% 12%);
  }
  .brand {
    position: absolute; left: 37px; top: 10px; width: 100px;
    display: flex; flex-direction: column; align-items: center; gap: 10px;
  }
  .brand-mark { width: 26px; height: 26px; border: 1.5px solid var(--gold); }
  .brand-name { font-size: 11px; font-weight: 400; color: var(--gold); white-space: nowrap; letter-spacing: 0.5px; }
  .main-nav { position: absolute; left: 563px; top: 240px; }
  .nav-link {
    position: absolute; top: 33px; font-size: 12px; font-weight: 400; color: var(--white); white-space: nowrap;
  }
  .nav-link.is-active { color: var(--gold); }
  .btn {
    position: absolute; display: flex; align-items: center; justify-content: center;
    background: var(--gold); color: var(--white); font-size: 12px; font-weight: 400;
  }
  .btn-nav { left: 925px; top: 21px; width: 114px; height: 38px; }
  .hero-accent { position: absolute; left: 47px; top: 122px; width: 2px; height: 86px; background: var(--gold); }
  .hero-title {
    position: absolute; left: 38px; top: 215px;
    font-size: 68px; font-style: italic; font-weight: 600; line-height: 87px; color: var(--white);
  }
  .hero-text {
    position: absolute; left: 716px; top: 228px; width: 325px;
    font-size: 13.2px; font-style: italic; line-height: 20.2px; color: var(--white);
  }
  .btn-hero { left: 716px; top: 427px; width: 113px; height: 38px; }

  .welcome-accent { position: absolute; left: 38px; top: 651px; width: 2px; height: 36px; background: var(--gold); }
  .welcome-title {
    position: absolute; left: 59px; top: 650px; font-size: 29px; font-style: italic; font-weight: 600; white-space: nowrap;
  }
  .welcome-text {
    position: absolute; left: 38px; top: 712px; width: 1010px;
    font-size: 14px; font-style: italic; line-height: 18px; color: var(--body);
  }
  .kitchen-photo {
    position: absolute; left: 38px; top: 772px; width: 1000px; height: 219px;
    background: linear-gradient(180deg, #f1f1ef 0%, #e6e6e3 50%, #cfcfcc 100%);
  }
</style>
</head>
<body>
  <div class="gold-band"></div>

  <section class="experience-panel">
    <h2 class="experience-title">Irreplaceable Experience</h2>
    <div class="experience-rule"></div>
    <p class="experience-text">We are committed to providing an unforgettable stay that exceeds your expectations and leaves lasting memories.</p>
  </section>
  <div class="lounge-photo" role="img" aria-label="Guest relaxing with a cup of tea in a softly lit lounge"></div>

  <section class="side-panel">
    <div class="side-rule"></div>
    <p class="side-text">t meet stand</p>
  </section>
  <div class="pool-photo" role="img" aria-label="Indoor pool with warm wood-slat walls"></div>

  <main class="home-page">
    <header class="hero">
      <div class="hero-photo" role="img" aria-label="High-rise residential tower against a cloudy sky"></div>
      <div class="brand">
        <span class="brand-mark"></span>
        <span class="brand-name">Velmor Spire Nine</span>
      </div>
      <nav>
        <span class="nav-link is-active" style="left:563px">Home</span>
        <span class="nav-link" style="left:636px">About Us</span>
        <span class="nav-link" style="left:729px">Room</span>
        <span class="nav-link" style="left:802px">Experience</span>
        <span class="btn btn-nav">Contact Us</span>
      </nav>
      <div class="hero-accent"></div>
      <h1 class="hero-title">Privileges<br>and<br>Comfort</h1>
      <p class="hero-text">a place where warmth and luxury come together. Explore a blissful living or working experience in this special location. With the best facilities and stunning views, Velmor Spire invites you to experience the coolness of an elegant and inspiring lifestyle. Come discover magic in every corner, and experience the perfect balance of modern comfort and traditional charm, only at Velmor Spire.</p>
      <span class="btn btn-hero">Contact Us</span>
    </header>

    <div class="welcome-accent"></div>
    <h2 class="welcome-title">Welcome to Velmor Spire!</h2>
    <p class="welcome-text">We are more than just a building; we are the home of your dreams. At Velmor Spire, we are committed to providing an unforgettable living and working experience, where comfort meets luxury.</p>
    <div class="kitchen-photo" role="img" aria-label="Bright modern kitchen with white cabinets and black pendant lamps"></div>
  </main>
</body>
</html>
```